Cover page and letterhead for athlete development program

We require an exciting and dynamic cover page with a second page letterhead in a word doc format for us to use as professional stationery for letter merges and portfolio documents. We are an athlete preparation company that specialises in training up and coming sports representatives in the fitness and sports science industry. We work with athletes from ages 13 - 24 mainly. If we could have images on the cover page from the sports of:
Rugby League
Rugby Union
Hockey
Cricket
AFL
Soccer
Track and Field
Netball
Basketball
Golf
Weight training

This would be a great start. Thank you

```html
<!DOCTYPE html>
<html lang="en">
<head>
<meta charset="utf-8">
<title>Rising Stride Letterhead</title>
<link href="https://fonts.googleapis.com/css2?family=Arimo:wght@400;700&display=swap" rel="stylesheet">
<style>
  :root {
    --backdrop: #d9dcde;
    --paper: #ffffff;
    --ink: #1a1a1a;
    --body-grey: #7a7a7a;
    --muted: #8e8e8e;
    --gold: #d89a2c;
    --silver: #cfcfcf;
    --charcoal: #2b2b2b;
  }
  * { box-sizing: border-box; margin: 0; padding: 0; }
  html, body { width: 1200px; height: 784px; overflow: hidden; }
  body {
    background: var(--backdrop);
    font-family: "Arimo", Arial, sans-serif;
    display: flex;
    align-items: center;
    justify-content: center;
  }
  .letterhead {
    position: relative;
    width: 530px;
    height: 750px;
    background: var(--paper);
    box-shadow: 0 4px 18px rgba(0,0,0,0.12);
    overflow: hidden;
  }
  .corner-accent {
    position: absolute;
    width: 120px;
    height: 90px;
    background: linear-gradient(135deg, var(--silver) 0%, var(--gold) 50%, var(--charcoal) 100%);
  }
  .corner-accent--top {
    top: 0;
    right: 0;
    clip-path: polygon(0 0, 100% 0, 100% 100%);
  }
  .corner-accent--bottom {
    bottom: 0;
    left: 0;
    clip-path: polygon(0 0, 100% 100%, 0 100%);
  }

  .brand {
    position: absolute;
    top: 64px;
    right: 40px;
    display: flex;
    align-items: center;
    gap: 8px;
  }
  .brand__mark { width: 14px; height: 14px; background: var(--gold); }
  .brand__name {
    font-size: 22px;
    font-weight: 700;
    letter-spacing: 1px;
    color: var(--ink);
  }
  .contact {
    position: absolute;
    top: 100px;
    right: 40px;
    text-align: right;
    font-style: normal;
    font-size: 7.5px;
    line-height: 1.6;
    color: var(--muted);
  }
  .contact__address { color: var(--ink); font-weight: 700; }
  .contact__row { display: flex; justify-content: flex-end; align-items: center; gap: 4px; }
  .contact__dot { width: 5px; height: 5px; border-radius: 50%; background: var(--muted); }

  .letter-body {
    position: absolute;
    top: 160px;
    left: 58px;
    width: 400px;
    font-size: 9.5px;
    line-height: 1.55;
    color: var(--body-grey);
  }
  .letter-body p { margin-bottom: 13px; }
  .signature {
    width: 150px;
    height: 48px;
    margin-top: 18px;
    margin-left: 60px;
    border-radius: 6px;
    background: linear-gradient(90deg, rgba(150,150,150,0.12), rgba(150,150,150,0.25), rgba(150,150,150,0.08));
  }
</style>
</head>
<body>
  <main class="letterhead">
    <div class="corner-accent corner-accent--top" role="img" aria-label="Decorative folded corner accent in silver, gold and charcoal"></div>

    <div class="brand">
      <span class="brand__mark"></span>
      <span class="brand__name">RISING STRIDE</span>
    </div>

    <address class="contact">
      <div class="contact__row contact__address"><span class="contact__dot"></span>100 Harbor Way, Ste 200, Lakeview, US 00010</div>
      <div class="contact__row"><span class="contact__dot"></span>000-000-0100 &nbsp;<span class="contact__dot"></span>000-000-0155</div>
      <div class="contact__row"><span class="contact__dot"></span>hello@risingstride.example</div>
      <div class="contact__row">www.risingstride.example</div>
    </address>

    <section class="letter-body">
      <p>Lorem Ipsum is simply dummy text of the printing and typesetting industry. Lorem Ipsum has been the industry's standard dummy text ever since the 1500s, when an unknown printer took a galley of type and scrambled it to make a type specimen book. It has survived not only five centuries, but also the leap into electronic typesetting, remaining essentially unchanged. It was popularised in the 1960s with the release of Typeworks sheets containing Lorem Ipsum passages, and more recently with desktop publishing software like PageCraft Studio including versions of Lorem Ipsum.</p>
      <p>It is a long established fact that a reader will be distracted by the readable content of a page when looking at its layout. The point of using Lorem Ipsum is that it has a more-or-less normal distribution of letters, as opposed to using 'Content here, content here', making it look like readable English. Many desktop publishing packages and web page editors now use Lorem Ipsum as their default model text, and a search for 'lorem ipsum' will uncover many web sites still in their infancy. Various versions have evolved over the years, sometimes by accident, sometimes on purpose (injected humour and the like).</p>
      <p>Contrary to popular belief, Lorem Ipsum is not simply random text. It has roots in a piece of classical Latin literature from 45 BC, making it over 2000 years old. Daniel Marlow, a Latin professor at Westbrook College in Lakeview, looked up one of the more obscure Latin words, consectetur, from a Lorem Ipsum passage, and going through the cites of the word in classical literature, discovered the undoubtable source. Lorem Ipsum comes from sections 1.10.32 and 1.10.33 of "de Finibus Bonorum et Malorum" structures, to generate Lorem Ipsum which looks reasonable. The generated Lorem Ipsum is therefore always free from repetition, injected humour, or non-characteristic words etc.</p>
      <div class="signature" role="img" aria-label="Handwritten signature of the sender"></div>
    </section>

    <div class="corner-accent corner-accent--bottom" role="img" aria-label="Decorative folded corner accent in silver, gold and charcoal"></div>
  </main>
</body>
</html>
```